Dental Practice Billboard Design

We are a newer dental practice in need of a simple but appealing billboard for our growing dental practice to attract new patients. The practice is owned by husband and wife dentists and is family friendly in a small town in Kentucky. We try to be very friendly and caring to our patients. Would prefer a blue background for the billboard and our tooth logo to be prominent. We are partial to the Patua One font used in the image below but please feel free to tweak it as you deem necessary. The shape of the uppercase D and lowercase g are why we like that font, so fonts with a similarly shaped “D” and “g” would work as well. Please include our phone number (555) 847-1390. Please see our website Harlowbrookdentistry.example for more info on the practice if needed. Thank you! Looking forward to seeing your creation.
Updates

The dimensions will be 12ft x 24ft (3.6576m x 7.3152m). Apologies for not including this in the original prompt. Thank you all for your submissions.

Industry/Entity Type

Dental

Font styles to use
Other font styles liked:
• Patua One

Colors
0054AA
0677BA
7BADD7
CADEEF
E8F1F8
0094D4
00A9DD
6FCCEA
C7EBF8
E9F6FB
00AB8E
00BBA5
67D7C9
C6EFE9
E9F9F6
59FF00
82FF00
B8FF75
E3FFCB
F4FFEA

Requirements
Must have
• Phone number, website, Logo, Practice name “Harlow Brook Dentistry”
Should not have
• A tagline or slogan

```html
<!DOCTYPE html>
<html lang="en">
<head>
<meta charset="utf-8">
<title>Harlow Brook Dentistry Billboard</title>
<link href="https://fonts.googleapis.com/css2?family=Montserrat:wght@700;800&family=Patua+One&display=swap" rel="stylesheet">
<style>
  :root {
    --navy: #06285e;
    --green: #1bb520;
    --white: #ffffff;
    --rule: rgba(27, 181, 32, 0.35);
    --stage: #e9edf2;
    --skin-light: #f1cdb8;
    --skin-mid: #dea48e;
    --lip: #d9787a;
  }
  * { box-sizing: border-box; margin: 0; padding: 0; }
  html, body { width: 1200px; height: 835px; overflow: hidden; }
  body { background: var(--stage); position: relative; }

  .billboard {
    position: absolute;
    left: 40px; top: 137px;
    width: 1120px; height: 560px;
    background: var(--navy);
    overflow: hidden;
  }
  .billboard__art { position: absolute; inset: 0; width: 1120px; height: 560px; }

  .content {
    position: absolute;
    left: 16px; top: 0;
    width: 660px; height: 560px;
    display: flex;
    flex-direction: column;
    justify-content: center;
    align-items: stretch;
  }
  .brand {
    display: flex;
    align-items: center;
    justify-content: center;
    gap: 24px;
  }
  .brand__dot {
    width: 124px; height: 124px;
    border-radius: 50%;
    background: var(--green);
    flex: none;
  }
  .brand__name {
    font-family: "Patua One", Georgia, serif;
    color: var(--white);
    line-height: 1;
    white-space: nowrap;
  }
  .brand__line--main { display: block; font-size: 74px; }
  .brand__line--sub { display: block; font-size: 46px; margin-top: 8px; }

  .rule {
    height: 1px;
    background: var(--rule);
    margin: 40px 0 22px;
  }

  .contact {
    display: flex;
    align-items: center;
    justify-content: center;
    gap: 16px;
    font-family: "Montserrat", Arial, sans-serif;
    font-weight: 700;
    color: var(--white);
  }
  .contact__item { display: flex; align-items: center; gap: 8px; white-space: nowrap; }
  .contact__phone { font-size: 26px; }
  .contact__web { font-size: 20px; }
  .contact__icon { width: 24px; height: 24px; flex: none; }
</style>
</head>
<body>
  <div class="billboard">
    <svg class="billboard__art" viewBox="0 0 1120 560" xmlns="http://www.w3.org/2000/svg">
      <defs>
        <radialGradient id="smileTone" cx="0.6" cy="0.55" r="0.65">
          <stop offset="0" stop-color="var(--lip)"/>
          <stop offset="0.45" stop-color="var(--skin-mid)"/>
          <stop offset="1" stop-color="var(--skin-light)"/>
        </radialGradient>
      </defs>
      <path class="accent-curve" d="M778 0 C680 130 660 380 668 560 L700 560 C692 380 712 130 810 0 Z" fill="var(--green)"/>
      <path class="photo-area" role="img" aria-label="Close-up photo of a smiling mouth with bright white teeth"
            d="M800 0 C702 130 682 380 690 560 L1120 560 L1120 0 Z" fill="url(#smileTone)"/>
    </svg>

    <div class="content">
      <div class="brand">
        <span class="brand__dot"></span>
        <h1 class="brand__name">
          <span class="brand__line--main">Harlow Brook</span>
          <span class="brand__line--sub">Dentistry</span>
        </h1>
      </div>

      <div class="rule"></div>

      <div class="contact">
        <span class="contact__item contact__phone">
          <svg class="contact__icon" viewBox="0 0 24 24" aria-hidden="true">
            <path d="M6.6 10.8a15 15 0 0 0 6.6 6.6l2.2-2.2a1 1 0 0 1 1-.25 11.4 11.4 0 0 0 3.6.57 1 1 0 0 1 1 1V20a1 1 0 0 1-1 1A17 17 0 0 1 3 4a1 1 0 0 1 1-1h3.5a1 1 0 0 1 1 1c0 1.25.2 2.45.57 3.57a1 1 0 0 1-.25 1z" fill="var(--green)"/>
          </svg>
          (555) 847-1390
        </span>
        <span class="contact__item contact__web">
          <svg class="contact__icon" viewBox="0 0 24 24" aria-hidden="true" fill="none" stroke="var(--green)" stroke-width="2">
            <circle cx="12" cy="12" r="9.5"/>
            <ellipse cx="12" cy="12" rx="4.2" ry="9.5"/>
            <path d="M2.5 12h19M4 7h16M4 17h16"/>
          </svg>
          Harlowbrookdentistry.example
        </span>
      </div>
    </div>
  </div>
</body>
</html>
```